Pressure Washing Hog Confinements

We clean and disinfect Hog confinements in-order to receive new pigs.

Needs to emphasis Clean Healthy barns (pigs), work done in timely manner, 100% satisfied, Bio-security rules followed. I do not have specific colors, no logo's.

Contact Information will be sent once design is agreed on.
Business Name - Brandt & Daughters Power Washing
Phone Number - Send latter
E-mail - Send latter
Web Address - Send latter

Target Market(s)

Farmers

Industry/Entity Type

Business

Requirements
Must have
• We are Insured
Bio-Security
100% Satisfied
Water Conservation

Size - 2 sided Postcard 8.5" x 5.5"
Nice to have
• I want to emphasize healthy and happy pigs because of a quality job done. Picture of pigs dose not need to be used but may be just an example.

Also attached is picture of a barn I would like to see used. on the back side. Every owner seeing this will know this is a hog barn and have an idea what we do.

```html
<!DOCTYPE html>
<html lang="en">
<head>
<meta charset="utf-8">
<title>Brandt &amp; Daughters Power Washing – Postcard</title>
<link rel="stylesheet" href="https://fonts.googleapis.com/css2?family=Ubuntu:wght@500&family=Roboto+Condensed:wght@400&family=Arimo:wght@400&display=swap">
<style>
  :root {
    --backdrop: #e9e6e1;
    --ink-black: #000000;
    --brand-green: #6cc04a;
    --deep-green: #2e9a3a;
    --band-green: #1f8a2c;
    --band-edge: #c9d92a;
    --white: #ffffff;
    --name-grey: #c9d3dc;
    --text-grey: #333333;
    --sky-top: #5f8fd0;
    --sky-low: #b9d0ee;
    --hazard-orange: #f07c1e;
  }
  * { box-sizing: border-box; margin: 0; padding: 0; }
  html, body { width: 1200px; height: 444px; overflow: hidden; }
  body { background: var(--backdrop); position: relative; }

  .postcard { position: absolute; width: 555px; height: 358px; overflow: hidden; box-shadow: 0 2px 6px rgba(0,0,0,.25); }

  /* Front */
  .postcard--front { left: 28px; top: 32px; background: var(--ink-black); }
  .front__panel { position: absolute; left: 0; top: 0; width: 256px; height: 302px; background: var(--ink-black); }
  .front__name { position: absolute; left: 26px; top: 32px; font: 500 24px/1 "Ubuntu", sans-serif; color: var(--name-grey); letter-spacing: .3px; white-space: nowrap; }
  .front__points { position: absolute; left: 26px; top: 99px; list-style: none; font: 400 21px/28px "Roboto Condensed", sans-serif; color: var(--brand-green); }
  .front__hazard { position: absolute; left: 26px; top: 262px; width: 33px; height: 33px; }
  .front__visual { position: absolute; left: 256px; top: 0; width: 299px; height: 302px; background: radial-gradient(circle at 55% 18%, #cfe6f7 0%, #6ea9d8 38%, #1f5fa0 80%, #174b84 100%); }
  .front__band { position: absolute; left: 0; top: 302px; width: 100%; height: 36px; background: linear-gradient(var(--band-green), #146f22); border-top: 2px solid var(--band-edge); border-bottom: 2px solid var(--band-edge); display: flex; align-items: center; justify-content: center; gap: 10px; font: 400 14px/1 "Arimo", sans-serif; color: var(--white); }
  .front__dot { width: 5px; height: 5px; border-radius: 50%; background: var(--band-edge); }

  /* Back */
  .postcard--back { left: 617px; top: 56px; background: var(--white); }
  .back__message { position: absolute; left: 21px; top: 20px; font: 400 16px/22px "Arimo", sans-serif; color: var(--deep-green); }
  .back__contact { position: absolute; left: 21px; top: 101px; font: 400 13px/18px "Arimo", sans-serif; color: var(--text-grey); }
  .back__indicia { position: absolute; left: 486px; top: 18px; width: 47px; height: 47px; border: 1px solid #222; display: flex; flex-direction: column; justify-content: center; align-items: center; font: 400 5.5px/7px "Arimo", sans-serif; color: #222; text-align: center; }
  .back__indicia::before { content: ""; position: absolute; inset: 2px; border: 1px solid #222; }
  .back__address { position: absolute; left: 439px; top: 90px; width: 94px; height: 46px; border: 1px solid #222; padding: 14px 0 0 11px; font: 400 8px/10px "Arimo", sans-serif; color: #222; }
  .back__rule { position: absolute; left: 0; top: 166px; width: 100%; height: 4px; background: linear-gradient(90deg, var(--band-green), var(--band-edge) 50%, var(--band-green)); }
  .back__photo { position: absolute; left: 0; top: 170px; width: 100%; height: 188px; background: linear-gradient(180deg, var(--sky-top) 0%, var(--sky-low) 55%, #d9d9d9 70%, #a9a39a 85%, #7d8a4f 100%); }
  .back__name { position: absolute; left: 21px; top: 196px; font: 500 27px/1 "Ubuntu", sans-serif; color: var(--white); white-space: nowrap; }
</style>
</head>
<body>

<section class="postcard postcard--front">
  <div class="front__panel"></div>
  <h1 class="front__name">Brandt &amp; Daughters</h1>
  <ul class="front__points">
    <li>We are Insured</li>
    <li>Bio-Security</li>
    <li>100% Satisfied</li>
    <li>Water Conservation</li>
  </ul>
  <svg class="front__hazard" viewBox="0 0 33 33" aria-hidden="true">
    <rect width="33" height="33" fill="var(--hazard-orange)"/>
    <circle cx="16.5" cy="11" r="5.5" fill="none" stroke="#000" stroke-width="2"/>
    <circle cx="11" cy="20.5" r="5.5" fill="none" stroke="#000" stroke-width="2"/>
    <circle cx="22" cy="20.5" r="5.5" fill="none" stroke="#000" stroke-width="2"/>
    <circle cx="16.5" cy="17.5" r="2.5" fill="#000"/>
  </svg>
  <div class="front__visual" role="img" aria-label="Chrome water tap with a green seedling growing from its spout on a blue background"></div>
  <div class="front__band">
    <span>5550148273</span><span class="front__dot"></span>
    <span>info@brandtdaughters.com</span><span class="front__dot"></span>
    <span>www.brandtdaughters.com</span>
  </div>
</section>

<section class="postcard postcard--back">
  <p class="back__message">Clean Healthy barns (pigs), work done<br>in timely manner, 100% satisfied,<br>Bio-security rules followed</p>
  <p class="back__contact">5550148273<br>info@brandtdaughters.com<br>www.brandtdaughters.com</p>
  <div class="back__indicia">PRSRT STD<br>ECRWSS<br>U.S.POSTAGE<br>PAID<br>EDDM Retail</div>
  <div class="back__address">Local<br>Postal Customer</div>
  <div class="back__rule"></div>
  <div class="back__photo" role="img" aria-label="Long hog confinement barn with feed silos under a blue sky"></div>
  <h2 class="back__name">Brandt &amp; Daughters</h2>
</section>

</body>
</html>
```